business card - Helicopter Flight Services, Flight School, etc.

We need a business card design for a new helicopter service.

We offer Helicopter Flight Services, Aerial Filming & Photography, Flight School, and Helicopter Tours. In that order.

Summit BladeAir, Inc.
Dennis Tollerby
SummitBladeair@Kestmail.com
626-418-7352

Based at the Brenwick Airport in Van Nuys, CA. The final design should communicate integrity and safety. Pictures or logos at your discretion.

Card back side - surprise me.

```html
<!DOCTYPE html>
<html lang="en">
<head>
<meta charset="utf-8">
<title>Summit BladeAir, Inc. – Business Card</title>
<link rel="stylesheet" href="https://fonts.googleapis.com/css2?family=Open+Sans:wght@400;600;700&display=swap">
<style>
  :root {
    --page-bg: #e9e6e2;
    --card-dark: #0c0c0d;
    --card-dark-edge: #242426;
    --card-light: #ffffff;
    --brand-blue: #1f8fd6;
    --brand-blue-deep: #1773b8;
    --text-light: #ffffff;
    --text-soft: #d8d8d8;
  }
  * { box-sizing: border-box; margin: 0; padding: 0; }
  html, body {
    width: 1200px;
    height: 913px;
    overflow: hidden;
    background: var(--page-bg);
    font-family: "Open Sans", Arial, sans-serif;
  }
  .canvas {
    position: relative;
    width: 1200px;
    height: 913px;
  }
  .card {
    position: absolute;
    width: 525px;
    height: 300px;
    border-radius: 22px;
    box-shadow: 0 10px 28px rgba(0,0,0,0.22);
    overflow: hidden;
  }

  /* Front side */
  .card-front {
    left: 70px;
    top: 140px;
    background: linear-gradient(160deg, var(--card-dark-edge) 0%, var(--card-dark) 55%);
  }
  .front-brand {
    position: absolute;
    left: 38px;
    top: 160px;
    display: flex;
    align-items: center;
    gap: 14px;
  }
  .brand-square {
    flex: none;
    width: 40px;
    height: 40px;
    background: var(--brand-blue);
  }
  .front-brand .brand-name {
    display: block;
    width: 190px;
    color: var(--text-light);
    font-weight: 700;
    font-size: 20px;
    line-height: 24px;
    letter-spacing: 0.5px;
    text-transform: uppercase;
  }
  .front-contact {
    position: absolute;
    left: 305px;
    top: 112px;
  }
  .contact-name {
    color: var(--text-light);
    font-weight: 700;
    font-size: 19px;
    letter-spacing: 0.3px;
  }
  .contact-role {
    color: var(--brand-blue);
    font-size: 13px;
    margin: 2px 0 8px;
  }
  .contact-line {
    display: flex;
    align-items: center;
    gap: 7px;
    color: var(--text-soft);
    font-size: 12.5px;
    line-height: 20px;
    white-space: nowrap;
  }
  .contact-line svg { flex: none; }

  /* Back side */
  .card-back {
    left: 605px;
    top: 470px;
    background: var(--card-light);
    display: flex;
    flex-direction: column;
    align-items: center;
    justify-content: center;
    gap: 28px;
  }
  .back-brand {
    display: flex;
    align-items: center;
    gap: 16px;
  }
  .back-brand .brand-square { width: 52px; height: 52px; }
  .back-brand .brand-name {
    color: var(--brand-blue-deep);
    font-weight: 700;
    font-size: 28px;
    letter-spacing: 0.5px;
    text-transform: uppercase;
  }
  .service-list {
    list-style: none;
    text-align: center;
    color: var(--brand-blue);
    font-size: 15px;
    line-height: 21px;
  }
</style>
</head>
<body>
<main class="canvas">
  <section class="card card-front" aria-label="Card front">
    <div class="front-brand">
      <span class="brand-square" aria-hidden="true"></span>
      <span class="brand-name">Summit BladeAir, Inc.</span>
    </div>
    <div class="front-contact">
      <p class="contact-name">Dennis Tollerby</p>
      <p class="contact-role">Owner</p>
      <p class="contact-line">
        <svg width="11" height="11" viewBox="0 0 24 24" aria-hidden="true"><path fill="#1f8fd6" d="M6.6 10.8a15.1 15.1 0 0 0 6.6 6.6l2.2-2.2c.3-.3.7-.4 1-.2 1.1.4 2.3.6 3.6.6.6 0 1 .4 1 1V20c0 .6-.4 1-1 1A17 17 0 0 1 3 4c0-.6.4-1 1-1h3.5c.6 0 1 .4 1 1 0 1.3.2 2.5.6 3.6.1.3 0 .7-.2 1z"/></svg>
        626-418-7352
      </p>
      <p class="contact-line">
        <svg width="12" height="10" viewBox="0 0 24 18" aria-hidden="true"><rect x="1.5" y="1.5" width="21" height="15" rx="2" fill="none" stroke="#1f8fd6" stroke-width="2.5"/><path d="M2 3l10 7 10-7" fill="none" stroke="#1f8fd6" stroke-width="2.5"/></svg>
        SummitBladeair@Kestmail.com
      </p>
    </div>
  </section>

  <section class="card card-back" aria-label="Card back">
    <div class="back-brand">
      <span class="brand-square" aria-hidden="true"></span>
      <span class="brand-name">Summit BladeAir</span>
    </div>
    <ul class="service-list">
      <li>Aerial Filming &amp; Photography</li>
      <li>Flight School</li>
      <li>Helicopter Tours (In that order)</li>
    </ul>
  </section>
</main>
</body>
</html>
```